Veltrano.co - Polar Expeditions Specialists

We need a modern, visually striking business card for Veltrano.co, a company specialized in selling expedition cruises to the most remote regions on Earth, with a focus on the Arctic and Antarctica. The design should instantly communicate that the cardholder is an expert in polar travel. Use clean, premium aesthetics with cool tones like icy blue and white, possibly incorporating polar imagery (ice, glaciers, penguins, etc.)

Attached the logo

Contact Information for Business Card

Feels high-end and trustworthy.. Visually memorable — encourages people to keep it

Colors
0054AA
0677BA
7BADD7
CADEEF
E8F1F8

Requirements
Must have
• ice, glaciers, penguins, montains
Nice to have
• modern, transparente,

```html
<!DOCTYPE html>
<html lang="en">
<head>
<meta charset="utf-8">
<title>Veltrano.co – Business Card</title>
<link href="https://fonts.googleapis.com/css2?family=Poppins:wght@600;700&family=Arimo:wght@400;700&display=swap" rel="stylesheet">
<style>
  :root {
    --page-bg: #e6e9ed;
    --card-white: #f7f7f5;
    --brand-blue: #2f70b2;
    --accent-blue: #3f7fc0;
    --ink: #2b2b2b;
    --ink-soft: #6a6a6a;
    --white: #ffffff;
  }
  * { margin: 0; padding: 0; box-sizing: border-box; }
  html, body {
    width: 1200px; height: 1050px; overflow: hidden;
    background: var(--page-bg);
  }
  .sheet {
    width: 1200px; height: 1050px;
    display: flex; flex-direction: column; align-items: center; justify-content: center;
    gap: 60px;
  }
  .card {
    width: 760px; height: 434px;
    border-radius: 28px;
    position: relative;
    overflow: hidden;
    box-shadow: 0 6px 18px rgba(0,0,0,0.12);
  }
  .card-front { background: var(--card-white); }
  .card-back  { background: var(--brand-blue); }

  /* front */
  .holder { position: absolute; left: 90px; top: 150px; font-family: "Arimo", Arial, sans-serif; }
  .holder-name { color: var(--accent-blue); font-weight: 700; font-size: 34px; line-height: 1; }
  .holder-role { color: var(--ink-soft); font-size: 20px; margin-top: 4px; }
  .holder-phone { color: var(--ink); font-size: 22px; margin-top: 14px; }
  .address {
    position: absolute; left: 90px; top: 300px;
    font-family: "Arimo", Arial, sans-serif; font-size: 22px; line-height: 1.25; color: var(--ink);
  }
  .divider { position: absolute; left: 395px; top: 300px; width: 1.5px; height: 58px; background: var(--ink); }
  .online {
    position: absolute; left: 415px; top: 302px;
    font-family: "Arimo", Arial, sans-serif; font-size: 22px; line-height: 1.25; color: var(--ink);
  }
  .online-row { display: flex; align-items: center; gap: 10px; }
  .online-row svg { width: 20px; height: 20px; flex: none; }

  .front-mark {
    position: absolute; right: 70px; top: 110px;
    display: flex; align-items: center; gap: 12px;
    font-family: "Poppins", sans-serif; font-weight: 700; font-size: 34px; color: var(--accent-blue);
  }
  .front-mark .dot { width: 22px; height: 22px; border-radius: 50%; background: var(--accent-blue); }

  /* back */
  .back-brand {
    position: absolute; inset: 0;
    display: flex; flex-direction: column; align-items: center; justify-content: center;
    font-family: "Poppins", sans-serif; color: var(--white);
  }
  .back-mark { display: flex; align-items: center; gap: 16px; font-weight: 700; font-size: 72px; line-height: 1; }
  .back-mark .dot { width: 34px; height: 34px; border-radius: 50%; background: var(--white); }
  .tagline { font-weight: 600; font-size: 24px; margin-top: 14px; letter-spacing: 0.3px; }
</style>
</head>
<body>
<main class="sheet">
  <section class="card card-front" aria-label="Business card front">
    <div class="holder">
      <p class="holder-name">Marcus Hale</p>
      <p class="holder-role">President</p>
      <p class="holder-phone">(415) 5520-1987</p>
    </div>
    <p class="address">2716 Harbor Crest Lane<br>Bayview, NY 11020</p>
    <div class="divider"></div>
    <div class="online">
      <p class="online-row">
        <svg viewBox="0 0 20 20" aria-hidden="true"><rect x="1" y="4" width="18" height="12" rx="1.5" fill="var(--accent-blue)"/><path d="M2 5 L10 11 L18 5" fill="none" stroke="var(--white)" stroke-width="1.6"/></svg>
        name@veltrano.com
      </p>
      <p class="online-row">
        <svg viewBox="0 0 20 20" aria-hidden="true"><circle cx="10" cy="10" r="8.5" fill="var(--accent-blue)"/><path d="M1.5 10 H18.5 M10 1.5 C6 5 6 15 10 18.5 M10 1.5 C14 5 14 15 10 18.5" fill="none" stroke="var(--white)" stroke-width="1.2"/></svg>
        www.veltrano.com
      </p>
    </div>
    <div class="front-mark"><span class="dot"></span>Veltrano.co</div>
  </section>

  <section class="card card-back" aria-label="Business card back">
    <div class="back-brand">
      <div class="back-mark"><span class="dot"></span>Veltrano.co</div>
      <p class="tagline">Polar Expeditions Specialists</p>
    </div>
  </section>
</main>
</body>
</html>
```